Valtrane Capital LLC

Need Professional Business cards for New Investment Fund

Target Market(s)

High Quality investors

Industry/Entity Type

Financial

Contact Information for Business Card

Phone Number +1 555 284 6190
Name Lukas Varenko
Title Fund Manager
email lv@FundValtrane.com
Website www.FundValtrane.com

Colors

Designer to choose colors to be used in the design.

Requirements
Must have
• Must have our Logo and all of the above. Must be made so lettering and loge can be raised

```html
<!DOCTYPE html>
<html lang="en">
<head>
<meta charset="utf-8">
<title>Valtrane Capital – Business Card</title>
<link rel="stylesheet" href="https://fonts.googleapis.com/css2?family=Raleway:wght@400;500;600&family=Teko:wght@500&display=swap">
<style>
  :root {
    --bg: #1f1f1f;
    --green: #5bbb4a;
    --charcoal: #434f43;
    --white: #ffffff;
    --text-soft: #e9ede9;
  }
  * { box-sizing: border-box; margin: 0; padding: 0; }
  html, body {
    width: 1200px; height: 900px; overflow: hidden;
    background: var(--bg);
    font-family: "Raleway", sans-serif;
  }
  .canvas {
    position: relative; width: 1200px; height: 900px;
    display: flex; flex-direction: column; align-items: center;
    justify-content: center; gap: 30px;
  }
  .card {
    position: relative; width: 700px; height: 400px; overflow: hidden;
  }
  /* Front */
  .card--front { background: var(--green); }
  .brand {
    position: absolute; left: 0; right: 0; top: 172px;
    display: flex; align-items: center; justify-content: center; gap: 14px;
  }
  .brand__mark {
    width: 26px; height: 26px; background: var(--charcoal);
  }
  .brand__name {
    font-family: "Raleway", sans-serif; font-weight: 600;
    font-size: 38px; letter-spacing: 3px; color: var(--charcoal);
    text-transform: uppercase; white-space: nowrap;
  }
  .front-band {
    position: absolute; bottom: 0; left: 225px;
    width: 250px; height: 12px; background: var(--charcoal);
  }
  /* Back */
  .card--back { background: var(--charcoal); }
  .holder {
    position: absolute; left: 60px; top: 270px; text-align: left;
  }
  .holder__name {
    font-family: "Teko", sans-serif; font-weight: 500;
    font-size: 38px; line-height: 1; color: var(--white);
    text-transform: uppercase; letter-spacing: 0.5px; white-space: nowrap;
  }
  .holder__title {
    font-size: 19px; color: var(--text-soft); margin-top: 2px; white-space: nowrap;
  }
  .divider {
    position: absolute; left: 268px; top: 262px;
    width: 2px; height: 80px; background: var(--green);
  }
  .contacts {
    position: absolute; left: 292px; top: 262px;
    list-style: none; display: flex; flex-direction: column; gap: 6px;
  }
  .contacts__item {
    display: flex; align-items: center; gap: 12px;
    font-size: 19px; color: var(--white); line-height: 22px; white-space: nowrap;
  }
  .contacts__icon { width: 16px; height: 16px; flex: none; }
  .stripe {
    position: absolute; left: 0; right: 0; bottom: 0; height: 14px;
  }
</style>
</head>
<body>
<main class="canvas">
  <section class="card card--front" aria-label="Card front">
    <div class="brand">
      <span class="brand__mark"></span>
      <span class="brand__name">Valtrane</span>
    </div>
    <div class="front-band"></div>
  </section>

  <section class="card card--back" aria-label="Card back">
    <div class="holder">
      <h1 class="holder__name">Lukas Varenko</h1>
      <p class="holder__title">Title Fund Manager</p>
    </div>
    <div class="divider"></div>
    <ul class="contacts">
      <li class="contacts__item">
        <svg class="contacts__icon" viewBox="0 0 16 16"><path d="M4 1.5l2.2 3-1.3 1.6a9 9 0 0 0 5 5l1.6-1.3 3 2.2-1.4 2.4C8 14.2 1.8 8 1.6 2.9z" fill="var(--green)"/></svg>
        <span>+1 555 284 6190</span>
      </li>
      <li class="contacts__item">
        <svg class="contacts__icon" viewBox="0 0 16 16"><rect x="1.5" y="3.5" width="13" height="9" fill="none" stroke="var(--green)" stroke-width="1.4"/><path d="M1.5 3.5L8 9l6.5-5.5" fill="none" stroke="var(--green)" stroke-width="1.4"/></svg>
        <span>lv@FundValtrane.com</span>
      </li>
      <li class="contacts__item">
        <svg class="contacts__icon" viewBox="0 0 16 16" fill="none" stroke="var(--green)" stroke-width="1.3"><circle cx="8" cy="8" r="6.5"/><ellipse cx="8" cy="8" rx="3" ry="6.5"/><path d="M1.5 8h13M2.5 4.8h11M2.5 11.2h11"/></svg>
        <span>www.FundValtrane.com</span>
      </li>
    </ul>
    <svg class="stripe" viewBox="0 0 700 14" preserveAspectRatio="none">
      <polygon points="0,0 330,0 334,14 0,14" fill="var(--green)"/>
      <polygon points="338,0 700,0 700,14 342,14" fill="var(--white)"/>
    </svg>
  </section>
</main>
</body>
</html>
```